KRL Stationery Design Project

Dear Designers,
We need a new stationery design for company to match our new logo.
Designers should provide a design for the following:
1. Business Card: 3.5x2 Inches.
2. Letterhead: A4 size.
3. Envelops: 25x35.5 Cm.
You can keep the Arabic name at the bottom of the logo Or you can use the separate attached Arabic Name.
Please refer to the attached logo guide for design information.
Sample Business Card information:
Name: Tarek Sowan
Position: Operation Manager
Tel: +966 920007164 Ex. 500
Fax: +966 (3)8842617
Mob: +966 (5)00263817
email: tarek@krl-example.com.sa
URL: www.krl-example.com.sa
Address:
Nakheel Heights, Suite 718
Zayed bin Omar Str.
Khobar, 31847
Saudi Arabia
Updates
Dear All,
Please note, we had uploaded our logo along with Arabic writing in Adobe illustrator format (.ai).
Regards,
Karim
Dear All,
A sample data for the business card had been added as per your request.
Regards,
Karim

```html
<!DOCTYPE html>
<html lang="en">
<head>
<meta charset="UTF-8">
<title>KRL Envelope</title>
<link rel="stylesheet" href="https://fonts.googleapis.com/css2?family=Noto+Sans+Arabic:wght@700&family=Open+Sans:ital,wght@0,400;0,700;1,400&display=swap">
<style>
  :root {
    --backdrop: #bdbdbd;
    --paper: #ffffff;
    --brand-navy: #1e3a5f;
    --text-grey: #3a3a3a;
    --watermark: #f0f0f0;
    --edge-shadow: rgba(0, 0, 0, 0.18);
  }
  * { margin: 0; padding: 0; box-sizing: border-box; }
  html, body {
    width: 1200px;
    height: 900px;
    overflow: hidden;
    background: var(--backdrop);
    font-family: "Open Sans", "Noto Sans Arabic", Arial, sans-serif;
  }
  .canvas {
    position: relative;
    width: 1200px;
    height: 900px;
  }
  .envelope {
    position: absolute;
    left: 100px;
    top: 98px;
    width: 1000px;
    height: 704px;
    background: var(--paper);
    box-shadow: 0 6px 18px var(--edge-shadow);
    overflow: hidden;
  }
  .brand {
    position: absolute;
    left: 48px;
    top: 40px;
    display: flex;
    flex-direction: column;
    align-items: flex-start;
    gap: 6px;
  }
  .brand-row {
    display: flex;
    align-items: center;
    gap: 12px;
  }
  .brand-square {
    width: 30px;
    height: 30px;
    background: var(--brand-navy);
  }
  .brand-name {
    font-size: 40px;
    font-weight: 700;
    color: var(--brand-navy);
    letter-spacing: 1px;
    line-height: 1;
  }
  .brand-name-arabic {
    font-family: "Noto Sans Arabic", "Open Sans", sans-serif;
    font-size: 24px;
    font-weight: 700;
    color: var(--brand-navy);
    line-height: 1.2;
    align-self: stretch;
    text-align: right;
  }
  .return-address {
    position: absolute;
    left: 48px;
    bottom: 56px;
    font-size: 11px;
    line-height: 1.4;
    color: var(--text-grey);
    font-style: normal;
  }
  .return-address .web {
    color: var(--brand-navy);
  }
  .watermark {
    position: absolute;
    right: 40px;
    bottom: -30px;
    font-size: 220px;
    font-weight: 700;
    line-height: 1;
    letter-spacing: 8px;
    color: var(--watermark);
    user-select: none;
  }
</style>
</head>
<body>
  <main class="canvas">
    <section class="envelope" aria-label="KRL envelope">
      <span class="watermark" aria-hidden="true">KRL</span>
      <header class="brand">
        <div class="brand-row">
          <span class="brand-square" aria-hidden="true"></span>
          <span class="brand-name">KRL</span>
        </div>
        <span class="brand-name-arabic" lang="ar" dir="rtl">كي آر إل</span>
      </header>
      <address class="return-address">
        Nakheel Heights, Suite 718<br>
        Zayed bin Omar Str.<br>
        Khobar, 31847<br>
        Saudi Arabia<br>
        <span class="web">www.krl-example.com.sa</span>
      </address>
    </section>
  </main>
</body>
</html>
```